Construction business card

I need a new business card, they can connect with my logo, brand.
What we do is residential house , design and build
I like: Navy blue / black
I attached our logo, brand,
and, some idea for business card.

```html
<!DOCTYPE html>
<html lang="en">
<head>
<meta charset="utf-8">
<title>Harlow Ridge Builders – Business Card</title>
<link rel="stylesheet" href="https://fonts.googleapis.com/css2?family=Archivo:wght@400;600;800&display=swap">
<style>
  :root {
    --stage: #4a4a4c;
    --card: #262628;
    --card-edge: #1c1c1e;
    --brand-blue: #3a86d4;
    --ink: #ffffff;
    --ink-soft: #d8d8da;
  }
  * { box-sizing: border-box; margin: 0; padding: 0; }
  html, body {
    width: 1200px; height: 875px; overflow: hidden;
    background: var(--stage);
    font-family: "Archivo", Arial, sans-serif;
  }
  .canvas {
    position: relative; width: 1200px; height: 875px;
  }
  .card {
    position: absolute;
    width: 540px; height: 309px;
    top: 283px;
    background: var(--card);
    border-radius: 18px;
    box-shadow: 0 18px 40px rgba(0,0,0,.45);
    overflow: hidden;
  }
  .card--front { left: 40px; }
  .card--back { left: 620px; }

  /* Front */
  .brand-lockup {
    position: absolute; inset: 0;
    display: flex; align-items: center; justify-content: center; gap: 12px;
  }
  .brand-mark {
    width: 22px; height: 22px; background: var(--brand-blue);
  }
  .brand-name {
    color: var(--ink);
    font-weight: 800; font-size: 34px;
    letter-spacing: .5px; text-transform: uppercase; line-height: 1;
  }

  /* Back */
  .accent-tab {
    position: absolute; right: 0; top: 26px;
    width: 12px; height: 34px; background: var(--brand-blue);
  }
  .person {
    position: absolute; right: 28px; top: 26px; text-align: right;
  }
  .person-name {
    color: var(--brand-blue); font-weight: 800; font-size: 21px;
    text-transform: uppercase; letter-spacing: .3px; line-height: 1.1;
  }
  .person-role {
    color: var(--ink); font-size: 12px; font-weight: 400; margin-top: 2px;
  }
  .brand-lockup--small {
    inset: auto; left: 34px; top: 110px; justify-content: flex-start; gap: 8px;
  }
  .brand-lockup--small .brand-mark { width: 12px; height: 12px; }
  .brand-lockup--small .brand-name { font-size: 18px; }
  .contact {
    position: absolute; left: 34px; top: 160px;
    color: var(--ink); font-size: 12.5px; line-height: 1.35;
  }
  .contact-address { margin-bottom: 8px; }
  .contact-list { list-style: none; }
  .contact-list li { display: flex; align-items: center; gap: 7px; margin-bottom: 3px; }
  .contact-icon { width: 11px; height: 11px; flex: none; }
</style>
</head>
<body>
<main class="canvas">

  <section class="card card--front" aria-label="Card front">
    <div class="brand-lockup">
      <span class="brand-mark"></span>
      <span class="brand-name">Harlow Ridge Builders</span>
    </div>
  </section>

  <section class="card card--back" aria-label="Card back">
    <span class="accent-tab"></span>
    <div class="person">
      <p class="person-name">Dana Whitfield</p>
      <p class="person-role">CEO/Founder</p>
    </div>

    <div class="brand-lockup brand-lockup--small">
      <span class="brand-mark"></span>
      <span class="brand-name">Harlow Ridge Builders</span>
    </div>

    <div class="contact">
      <p class="contact-address">27 Elmstone Rd,<br>Kestrel Park, VIC 3190</p>
      <ul class="contact-list">
        <li>
          <svg class="contact-icon" viewBox="0 0 12 12" aria-hidden="true"><path d="M2.5 1 4.5 1 5.3 3.4 4 4.4C4.6 5.8 6.2 7.4 7.6 8L8.6 6.7 11 7.5 11 9.5C11 10.3 10.3 11 9.5 11 5 11 1 7 1 2.5 1 1.7 1.7 1 2.5 1Z" fill="var(--brand-blue)"/></svg>
          0400 555 018
        </li>
        <li>
          <svg class="contact-icon" viewBox="0 0 12 12" aria-hidden="true"><rect x="0.5" y="2.5" width="11" height="7.5" rx="1" fill="var(--brand-blue)"/><path d="M1 3 6 7 11 3" fill="none" stroke="var(--card)" stroke-width="1"/></svg>
          info@harlowridgebuilders.com.au
        </li>
        <li>
          <svg class="contact-icon" viewBox="0 0 12 12" aria-hidden="true"><circle cx="6" cy="6" r="5.2" fill="none" stroke="var(--brand-blue)" stroke-width="1.3"/><ellipse cx="6" cy="6" rx="2.2" ry="5.2" fill="none" stroke="var(--brand-blue)" stroke-width="1"/><path d="M1 6H11" stroke="var(--brand-blue)" stroke-width="1"/></svg>
          harlowridgebuilders.com.au
        </li>
      </ul>
    </div>
  </section>

</main>
</body>
</html>
```